Larkfield Ridge Management

I need a professional website. My current website is larkfieldridgemanagement.com and I hate it. It was created with some AI tool very quickly because I needed a site up and running with no advanced notice. I’m open to all designs .. I trust you, the professionals will deliver the results I’m anxiously awaiting! :)

```html
<!DOCTYPE html>
<html lang="en">
<head>
<meta charset="utf-8">
<title>Larkfield Ridge Management</title>
<link href="https://fonts.googleapis.com/css2?family=Roboto:wght@500;700&family=Montserrat:wght@400;500;600;700&display=swap" rel="stylesheet">
<style>
:root{
  --navy:#233a63;
  --navy-deep:#1d3158;
  --red:#c8202c;
  --red-dark:#a8161f;
  --tan:#a88a62;
  --ink:#222;
  --grey-light:#f3f3f3;
  --grey-mid:#c3c3c3;
  --white:#fff;
}
*{box-sizing:border-box;margin:0;padding:0}
html,body{width:1200px;height:4223px;overflow:hidden}
body{position:relative;background:var(--white);font-family:'Montserrat',sans-serif;color:var(--ink)}
.abs{position:absolute}
.btn{position:absolute;display:flex;align-items:center;justify-content:center;background:linear-gradient(90deg,var(--red-dark),var(--red));color:var(--white);font:700 14px 'Montserrat',sans-serif;letter-spacing:.2px;text-transform:uppercase}
.heading{font-family:'Roboto',sans-serif;font-weight:700;color:var(--navy);text-transform:uppercase}
.heading-rule{position:absolute;height:3px;background:var(--red)}

/* hero */
.hero-photo{position:absolute;left:0;top:0;width:1200px;height:760px;background:radial-gradient(ellipse at 72% 42%,#efe3d3 0%,#e2d6c8 30%,#d8cfc4 55%,#e9e6e2 80%)}
.hero-mask{position:absolute;left:0;top:0}
.nav{position:absolute;top:72px;font:600 15px 'Montserrat',sans-serif;color:var(--navy-deep);text-transform:uppercase}
.nav.active{color:var(--red);border-bottom:2px solid var(--red);padding-bottom:2px}
.nav-brand{position:absolute;left:500px;top:66px;width:200px;text-align:center;font:700 17px/1.15 'Montserrat',sans-serif;color:var(--navy)}
.hero-title{position:absolute;left:111px;top:208px;font-size:49px;line-height:56px}
.hero-text{position:absolute;left:111px;top:330px;width:570px;font-size:19.5px;line-height:28px;color:#111}

/* about */
.about-brand{position:absolute;left:111px;top:900px;width:487px;height:370px;display:flex;align-items:center;justify-content:center;gap:24px}
.about-brand .mark{width:46px;height:46px;background:var(--red);flex:none}
.about-brand .name{font:700 46px/1.1 'Montserrat',sans-serif;color:var(--navy)}
.about-text p{font-size:16.5px;line-height:25.7px;text-align:justify;color:#333;margin-bottom:15px}
.photo{position:absolute}
.frame-line{position:absolute;border-color:var(--tan);border-style:solid}

/* services */
.svc-card{position:absolute;top:2190px;width:228px;height:352px;background:var(--white);box-shadow:0 2px 10px rgba(0,0,0,.06);text-align:center}
.svc-card.featured{background:linear-gradient(160deg,#2d4a7c,#1f3560 70%,#2a4068)}
.svc-icon{position:absolute;left:72px;top:40px}
.svc-title{position:absolute;top:138px;left:0;width:100%;font:700 15.5px 'Montserrat',sans-serif;color:var(--navy);text-transform:uppercase}
.svc-desc{position:absolute;top:166px;left:14px;right:14px;font-size:14.5px;line-height:23px;color:#333}
.featured .svc-title,.featured .svc-desc{color:var(--white)}
.svc-card .btn{left:41px;top:273px;width:146px;height:46px}
.featured .btn{background:var(--white);color:var(--red)}

/* testimonials */
.quote-card{position:absolute;top:2836px;width:300px;height:303px;background:var(--white);border-bottom:4px solid var(--red);border-radius:8px 8px 0 0}
.quote-mark{position:absolute;left:14px;top:18px;font:700 52px/1 'Roboto',sans-serif;color:var(--navy)}
.stars{position:absolute;left:30px;top:64px;color:var(--red);font-size:20px;letter-spacing:2px}
.quote-text{position:absolute;left:30px;top:106px;width:256px;font-size:16px;line-height:22.5px;color:#222}
.quote-name{position:absolute;left:30px;top:258px;font:600 15px 'Montserrat',sans-serif;color:var(--navy)}
.quote-name::after{content:"";position:absolute;left:0;top:-14px;width:36px;height:2px;background:var(--red)}
.dot{position:absolute;top:3178px;width:5px;height:5px;border-radius:50%;background:#e6e6e6}
.dot.on{background:var(--white);width:6px;height:6px}

/* contact */
.field{position:absolute;background:var(--white);border-radius:26px;box-shadow:0 2px 12px rgba(0,0,0,.09);display:flex;align-items:center;font-size:15px;color:#333}
.field .ico{width:52px;display:flex;justify-content:center;border-right:1px solid #ddd;height:26px;align-items:center}
.field span.label{padding-left:14px}
.field.message{border-radius:24px;align-items:flex-start;padding-top:20px}

/* footer */
.foot-title{position:absolute;top:3902px;font:700 16px 'Montserrat',sans-serif;color:var(--white);text-transform:uppercase}
.foot-title::after{content:"";position:absolute;left:0;top:26px;width:115px;height:2px;background:var(--red)}
.foot-text{position:absolute;font-size:14.5px;line-height:24px;color:var(--white)}
.foot-ico{position:absolute;left:308px;width:36px;height:36px;border-radius:50%;background:var(--white);display:flex;align-items:center;justify-content:center}
.foot-link{position:absolute;left:659px;font-size:15px;color:var(--white)}
.social{position:absolute;top:4046px;width:34px;height:34px;border-radius:50%;background:var(--white)}
.social.active{background:var(--red)}
</style>
</head>
<body>

<!-- HERO -->
<div class="hero-photo" role="img" aria-label="Photo of a small model house beside stacked coins and a glass jar of coins on a table"></div>
<svg class="hero-mask" width="1200" height="760" viewBox="0 0 1200 760">
  <polygon points="0,533 600,754 0,760" fill="#fff"/>
  <polygon points="1200,533 600,754 1200,760" fill="#fff"/>
  <polygon points="357,645 600,727 839,645 839,651 600,737 357,651" fill="var(--red)"/>
</svg>

<a class="nav active" style="left:111px">Home</a>
<a class="nav" style="left:197px">About Us</a>
<a class="nav" style="left:316px">Our Services</a>
<div class="nav-brand">Larkfield Ridge<br>Management</div>
<a class="nav" style="left:754px">Contact Us</a>
<a class="btn" style="left:900px;top:61px;width:188px;height:44px">Request a Quote</a>

<h1 class="heading hero-title">A true partner,<br>not just a vendor.</h1>
<p class="hero-text">The organization applies rigorously tested frameworks and data-driven methodologies to safeguard property value while elevating tenant experience.</p>
<a class="btn" style="left:111px;top:433px;width:146px;height:45px">Contact Us</a>

<!-- ABOUT -->
<div class="about-brand">
  <div class="mark"></div>
  <div class="name">Larkfield Ridge<br>Management</div>
</div>
<h2 class="heading abs" style="left:660px;top:828px;font-size:42px">About Us</h2>
<div class="heading-rule" style="left:660px;top:878px;width:76px"></div>
<div class="about-text abs" style="left:660px;top:908px;width:428px">
  <p>Our organization delivers comprehensive property management solutions that optimize asset performance and tenant satisfaction. By integrating advanced analytics with proven operational frameworks, our specialists ensure each property achieves sustained value appreciation.</p>
  <p>Drawing on decades of collective expertise, the team facilitates regulatory compliance, cost efficiency, and proactive maintenance. This disciplined approach enables owners to preserve capital, enhance occupancy rates, and demonstrate long-term resilience across diverse market conditions.</p>
</div>
<a class="btn" style="left:660px;top:1287px;width:146px;height:46px">Learn More</a>

<div class="frame-line" style="left:592px;top:1439px;width:194px;height:61px;border-width:4px 4px 0 0"></div>
<div class="frame-line" style="left:347px;top:1748px;width:134px;height:64px;border-width:0 0 4px 4px"></div>
<div class="photo" role="img" aria-label="Photo of a small model house and a young tree growing on stacks of coins" style="left:488px;top:1510px;width:592px;height:350px;background:linear-gradient(160deg,#6f7f4a,#9aa270 40%,#b9a98a 75%,#d7cbb8)"></div>
<div class="photo" role="img" aria-label="Photo of a wooden model house and documents on a desk with two business people talking behind" style="left:114px;top:1387px;width:474px;height:355px;border:6px solid #fff;background:linear-gradient(160deg,#5a5550,#8b7f74 45%,#c8b49a 75%,#e5ddd2)"></div>

<!-- SERVICES -->
<svg class="abs" style="left:0;top:1935px" width="1200" height="680" viewBox="0 1935 1200 680">
  <polygon points="0,1942 1088,2052 1200,2080 1200,2615 0,2615" fill="var(--grey-light)"/>
  <polygon points="792,2004 1200,1937 1200,2080 1088,2062 1088,2048" fill="var(--red)"/>
</svg>
<h2 class="heading abs" style="left:0;width:1200px;text-align:center;top:2090px;font-size:42px">Services Offered</h2>
<div class="heading-rule" style="left:562px;top:2139px;width:76px"></div>

<div class="svc-card" style="left:111px">
  <svg class="svc-icon" width="84" height="84" viewBox="0 0 84 84"><polygon points="42,2 78,22 78,62 42,82 6,62 6,22" fill="#fbe9ea"/><circle cx="42" cy="42" r="16" fill="none" stroke="var(--red)" stroke-width="6" stroke-dasharray="5 3"/><path d="M33 45 L42 36 L51 45 V52 H33Z" fill="var(--red)"/></svg>
  <div class="svc-title">Property Care</div>
  <div class="svc-desc">Describe important details like price, value, length of service, and why it's unique.</div>
  <a class="btn">Learn More</a>
</div>
<div class="svc-card" style="left:361px">
  <svg class="svc-icon" width="84" height="84" viewBox="0 0 84 84"><polygon points="42,2 78,22 78,62 42,82 6,62 6,22" fill="#fbe9ea"/><path d="M28 40 L42 26 L56 40 V56 H28Z" fill="var(--red)"/><circle cx="50" cy="52" r="7" fill="#fff" stroke="var(--red)" stroke-width="3"/></svg>
  <div class="svc-title">Tenant Services</div>
  <div class="svc-desc">Describe important details like price, value, length of service, and why it's unique.</div>
  <a class="btn">Learn More</a>
</div>
<div class="svc-card featured" style="left:611px" role="img" aria-label="Card background photo of a building in navy tint">
  <svg class="svc-icon" width="84" height="84" viewBox="0 0 84 84"><polygon points="42,2 78,22 78,62 42,82 6,62 6,22" fill="var(--red)"/><circle cx="42" cy="46" r="14" fill="none" stroke="#fff" stroke-width="5" stroke-dasharray="5 3"/><rect x="30" y="22" width="24" height="10" fill="#fff"/></svg>
  <div class="svc-title">Maintenance</div>
  <div class="svc-desc">Describe important details like price, value, length of service, and why it's unique.</div>
  <a class="btn">Learn More</a>
</div>
<div class="svc-card" style="left:861px">
  <svg class="svc-icon" width="84" height="84" viewBox="0 0 84 84"><polygon points="42,2 78,22 78,62 42,82 6,62 6,22" fill="#fbe9ea"/><circle cx="48" cy="38" r="10" fill="none" stroke="var(--red)" stroke-width="3"/><path d="M22 54 H40 L56 48 V58 L40 62 H22Z" fill="var(--red)"/><rect x="26" y="22" width="10" height="4" fill="var(--red)"/><rect x="26" y="29" width="10" height="4" fill="var(--red)"/></svg>
  <div class="svc-title">Investment Growth</div>
  <div class="svc-desc">Describe important details like price, value, length of service, and why it's unique.</div>
  <a class="btn">Learn More</a>
</div>

<!-- TESTIMONIALS -->
<svg class="abs" style="left:0;top:2610px" width="1200" height="630" viewBox="0 2610 1200 630">
  <polygon points="0,2836 600,2614 1200,2836 1200,3240 0,3240" fill="var(--grey-mid)"/>
  <polygon points="357,2716 600,2632 839,2716 839,2724 600,2648 357,2724" fill="var(--red)"/>
</svg>
<h2 class="abs" style="left:0;width:1200px;text-align:center;top:2744px;font:700 42px 'Roboto',sans-serif;color:#fff;text-transform:uppercase">Testimonials</h2>
<div class="abs" style="left:562px;top:2795px;width:76px;height:3px;background:#fff"></div>

<div class="quote-card" style="left:111px"><div class="quote-mark">“</div><div class="stars">★★★★★</div><p class="quote-text">Lorem ipsum dolor sit amet, conse ctetur adipiscing elit, sed do eiusm od tempor incididunt ut labore et dolore magna aliqua. Ut enim ad minim veniam, quisea.</p><div class="quote-name">- John Doe</div></div>
<div class="quote-card" style="left:449px"><div class="quote-mark">“</div><div class="stars">★★★★★</div><p class="quote-text">Lorem ipsum dolor sit amet, conse ctetur adipiscing elit, sed do eiusm od tempor incididunt ut labore et dolore magna aliqua. Ut enim ad minim veniam, quisea.</p><div class="quote-name">- John Doe</div></div>
<div class="quote-card" style="left:788px"><div class="quote-mark">“</div><div class="stars">★★★★★</div><p class="quote-text">Lorem ipsum dolor sit amet, conse ctetur adipiscing elit, sed do eiusm od tempor incididunt ut labore et dolore magna aliqua. Ut enim ad minim veniam, quisea.</p><div class="quote-name">- John Doe</div></div>

<div class="dot" style="left:566px"></div>
<div class="dot" style="left:581px"></div>
<div class="dot" style="left:596px"></div>
<div class="dot on" style="left:611px"></div>
<div class="dot" style="left:626px"></div>

<!-- CONTACT -->
<h2 class="heading abs" style="left:0;width:1200px;text-align:center;top:3346px;font-size:42px">Contact Us</h2>
<div class="heading-rule" style="left:562px;top:3395px;width:76px"></div>

<div class="field" style="left:180px;top:3439px;width:410px;height:51px"><div class="ico"><svg width="14" height="16" viewBox="0 0 14 16"><circle cx="7" cy="4" r="4" fill="var(--navy)"/><path d="M0 16 C0 9 14 9 14 16Z" fill="var(--navy)"/></svg></div><span class="label">Your Name</span></div>
<div class="field" style="left:180px;top:3504px;width:410px;height:51px"><div class="ico"><svg width="16" height="12" viewBox="0 0 16 12"><rect width="16" height="12" rx="1" fill="var(--navy)"/><path d="M0 1 L8 7 L16 1" stroke="#fff" stroke-width="1.5" fill="none"/></svg></div><span class="label">Email</span></div>
<div class="field" style="left:180px;top:3570px;width:410px;height:51px"><div class="ico"><svg width="14" height="14" viewBox="0 0 14 14"><path d="M2 0 L5 0 L6 4 L4 5.5 C5 8 6 9 8.5 10 L10 8 L14 9 L14 12 C14 13 13 14 12 14 C5 13 1 9 0 2 C0 1 1 0 2 0Z" fill="var(--navy)"/></svg></div><span class="label">Phone</span></div>
<div class="field message" style="left:606px;top:3439px;width:412px;height:182px"><div class="ico"><svg width="18" height="14" viewBox="0 0 18 14"><ellipse cx="7" cy="6" rx="7" ry="5" fill="var(--navy)"/><ellipse cx="12" cy="9" rx="6" ry="4.5" fill="var(--navy)" stroke="#fff" stroke-width="1"/></svg></div><span class="label">Your Message</span></div>
<a class="btn" style="left:513px;top:3647px;width:174px;height:47px">Send Message</a>

<!-- FOOTER -->
<svg class="abs" style="left:0;top:3745px" width="1200" height="478" viewBox="0 3745 1200 478">
  <polygon points="0,3749 410,3826 110,3862 110,3876 0,3895" fill="var(--red)"/>
  <polygon points="0,3895 110,3876 110,3862 1200,3749 1200,4223 0,4223" fill="var(--navy)"/>
</svg>

<div class="abs" style="left:111px;top:3985px;width:160px;font:700 19px/1.25 'Montserrat',sans-serif;color:#fff;text-align:center">Larkfield Ridge<br>Management</div>

<div class="foot-title" style="left:308px">Contact Us</div>
<div class="foot-ico" style="top:3970px"><svg width="12" height="16" viewBox="0 0 12 16"><path d="M6 0 C2.7 0 0 2.6 0 6 C0 10 6 16 6 16 C6 16 12 10 12 6 C12 2.6 9.3 0 6 0Z" fill="var(--red)"/><circle cx="6" cy="6" r="2.2" fill="#fff"/></svg></div>
<div class="foot-text" style="left:364px;top:3962px">465, Lorum Ipsum Dolore,<br>LARKFIELD - RIDGETON</div>
<div class="foot-ico" style="top:4031px"><svg width="14" height="14" viewBox="0 0 14 14"><path d="M2 0 L5 0 L6 4 L4 5.5 C5 8 6 9 8.5 10 L10 8 L14 9 L14 12 C14 13 13 14 12 14 C5 13 1 9 0 2 C0 1 1 0 2 0Z" fill="var(--red)"/></svg></div>
<div class="foot-text" style="left:364px;top:4022px">Call Us:<br>+1 (888) 888 8888</div>
<div class="foot-ico" style="top:4092px"><svg width="16" height="12" viewBox="0 0 16 12"><rect width="16" height="12" rx="1" fill="var(--red)"/><path d="M0 1 L8 7 L16 1" stroke="#fff" stroke-width="1.5" fill="none"/></svg></div>
<div class="foot-text" style="left:364px;top:4082px">Email Us:<br>info@larkfieldridgemanagement.com</div>

<div class="foot-title" style="left:659px">Quick Links</div>
<a class="foot-link" style="top:3967px">Home</a>
<a class="foot-link" style="top:4003px">About Us</a>
<a class="foot-link" style="top:4039px">Services</a>
<a class="foot-link" style="top:4075px">Projects</a>
<a class="foot-link" style="top:4111px">Contact Us</a>

<div class="foot-title" style="left:829px">Newsletter</div>
<div class="abs" style="left:829px;top:3973px;width:259px;height:46px;background:#fff;display:flex;align-items:center;justify-content:space-between;padding:0 16px;font-size:14px;color:#333">Email Address<svg width="16" height="16" viewBox="0 0 16 16"><path d="M0 7 L16 0 L10 16 L7 9Z" fill="var(--red)"/></svg></div>
<div class="social active" style="left:830px" aria-label="Social profile link"></div>
<div class="social" style="left:870px" aria-label="Social profile link"></div>
<div class="social" style="left:909px" aria-label="Social profile link"></div>

<div class="abs" style="left:111px;top:4158px;width:977px;height:1px;background:rgba(255,255,255,.25)"></div>
<div class="abs" style="left:0;width:1200px;top:4180px;text-align:center;font-size:13px;color:#fff">Copyright © 2026 &nbsp;/&nbsp; All Rights Reserved &nbsp;/&nbsp; Privacy Policy</div>

</body>
</html>
```